New Business Card for Web Design/Internet Marketing Company

Looking for a great looking new business card. We are a 10 year old web design, internet marketing and website management company that works mostly with small businesses.

Our new card needs to better match the colors and style of our website, be bold, extremely usable and slightly edgy.

Target Market(s)

Small/Medium businesses that have websites

Industry/Entity Type

Internet

Requirements
Must have
• Front and back design, full color, rounded corners please

Must use the colors/style of our website (JPG provided)

INFO FOR CARDS (as readable as possible please)
Mark Lenner
President/CEO
mark@trelvanmedia.example
Phone: 520-381-7459
Toll Free: 866-381-7459
Address: 4315 W. Calloway Ave. Ste. 140, Tucson, AZ 85792

THINGS I WANT TO PROMOTE (if there is room):
1. Our Website - www.trelvanmedia.example

2. Social Media
Twitter: @trelvanmedia
Facebook: www.facebook.com/trelvanmedia

3. Our Services
Web Design
Internet Marketing
Website Management

```html
<!DOCTYPE html>
<html lang="en">
<head>
<meta charset="utf-8">
<title>Trelvan Media – Business Card Front and Back</title>
<link rel="stylesheet" href="https://fonts.googleapis.com/css2?family=Source+Sans+3:wght@400;600;700&display=swap">
<style>
  :root {
    --backdrop: #ececec;
    --card: #ffffff;
    --card-edge: #d6d6d6;
    --orange: #f0862f;
    --blue: #1a8fc9;
    --grey: #555a5f;
    --rule: #c9c9c9;
    --font-main: "Source Sans 3", "Myriad Pro", Arial, sans-serif;
  }
  * { box-sizing: border-box; margin: 0; padding: 0; }
  html, body {
    width: 1200px; height: 1080px; overflow: hidden;
    background: var(--backdrop);
    font-family: var(--font-main);
  }
  .canvas { position: relative; width: 1200px; height: 1080px; }

  .card {
    position: absolute;
    width: 767px; height: 438px;
    background: var(--card);
    border: 1px solid var(--card-edge);
    border-radius: 10px;
    box-shadow: 0 4px 14px rgba(0,0,0,0.12);
    overflow: hidden;
  }
  .card--front { left: 83px; top: 75px; }
  .card--back  { left: 346px; top: 576px; }

  /* Brand: invented name as plain text with one plain circle */
  .brand { position: absolute; display: flex; align-items: center; justify-content: center; gap: 12px; }
  .brand__dot { width: 26px; height: 26px; border-radius: 50%; background: var(--orange); flex: none; }
  .brand__name { font-weight: 700; color: var(--blue); line-height: 1; white-space: nowrap; }

  .card--front .brand { left: 30px; top: 162px; width: 370px; }
  .card--front .brand__name { font-size: 46px; }

  .divider {
    position: absolute; left: 415px; top: 93px;
    width: 2px; height: 197px; background: var(--rule);
  }

  .contact { position: absolute; left: 445px; top: 106px; color: var(--grey); font-size: 19px; }
  .contact__list { list-style: none; }
  .contact__item { display: flex; align-items: center; gap: 10px; height: 28px; }
  .contact__item svg { width: 14px; height: 14px; flex: none; fill: var(--grey); }
  .contact__address { margin-top: 20px; line-height: 26px; font-style: normal; }

  .band { position: absolute; top: 364px; height: 6px; }
  .band--orange { left: 0; width: 36px; background: var(--orange); }
  .band--blue { left: 45px; right: 0; background: var(--blue); }

  .person {
    position: absolute; left: 0; right: 0; top: 386px;
    text-align: center; font-size: 21px; color: var(--blue);
  }
  .person__name { font-weight: 700; font-size: 24px; color: var(--orange); }

  /* Back */
  .card--back .brand { left: 0; right: 0; top: 118px; }
  .card--back .brand__name { font-size: 54px; }

  .services {
    position: absolute; left: 0; right: 0; top: 264px;
    list-style: none; text-align: center;
    color: var(--blue); font-weight: 700; font-size: 25px; line-height: 33px;
  }
  .services li { display: inline-block; margin: 0 10px; }
  .services li::before {
    content: ""; display: inline-block; width: 11px; height: 11px;
    border-radius: 50%; background: var(--orange);
    margin-right: 8px; vertical-align: 3px;
  }
  .services__break { display: block; height: 0; }

  .social {
    position: absolute; left: 0; right: 0; top: 370px;
    display: flex; justify-content: center; gap: 18px;
    color: var(--grey); font-size: 25px;
  }
  .social__item { display: flex; align-items: center; gap: 6px; }
  .social__mark { width: 20px; height: 20px; border-radius: 3px; background: var(--blue); }
</style>
</head>
<body>
<main class="canvas">

  <section class="card card--front" aria-label="Business card front">
    <div class="brand">
      <span class="brand__dot"></span>
      <span class="brand__name">Trelvan Media</span>
    </div>

    <div class="divider"></div>

    <div class="contact">
      <ul class="contact__list">
        <li class="contact__item">
          <svg viewBox="0 0 16 16" aria-hidden="true"><path d="M3.6 1 6 3.8 4.6 5.6c.9 2.2 3.6 4.9 5.8 5.8l1.8-1.4L15 12.4l-2 2.4C7.2 14.6 1.4 8.8 1.2 3z"/></svg>
          <span>866-381-7459</span>
        </li>
        <li class="contact__item">
          <svg viewBox="0 0 16 16" aria-hidden="true"><path d="M3.6 1 6 3.8 4.6 5.6c.9 2.2 3.6 4.9 5.8 5.8l1.8-1.4L15 12.4l-2 2.4C7.2 14.6 1.4 8.8 1.2 3z"/></svg>
          <span>520-381-7459</span>
        </li>
        <li class="contact__item">
          <svg viewBox="0 0 16 16" aria-hidden="true"><path d="M1 3h14v10H1z M2.5 4.5 8 9l5.5-4.5v-.2H2.5z" fill-rule="evenodd"/></svg>
          <span>mark@trelvanmedia.example</span>
        </li>
        <li class="contact__item">
          <svg viewBox="0 0 16 16" aria-hidden="true"><path d="M8 1a7 7 0 1 0 0 14A7 7 0 0 0 8 1zm0 1.5c.8 0 1.7 1.6 2 4H6c.3-2.4 1.2-4 2-4zM2.6 7.2h2.6v1.6H2.6zm8.2 0h2.6v1.6h-2.6zM6 9.5h4c-.3 2.4-1.2 4-2 4s-1.7-1.6-2-4z"/></svg>
          <span>www.trelvanmedia.example</span>
        </li>
      </ul>
      <address class="contact__address">
        4315 W. Calloway Ave. Ste. 140<br>
        Tucson, AZ 85792
      </address>
    </div>

    <div class="band band--orange"></div>
    <div class="band band--blue"></div>

    <p class="person"><span class="person__name">Mark Lenner ,</span> President/CEO</p>
  </section>

  <section class="card card--back" aria-label="Business card back">
    <div class="brand">
      <span class="brand__dot"></span>
      <span class="brand__name">Trelvan Media</span>
    </div>

    <ul class="services">
      <li>Web Design</li><li>Internet Marketing</li>
      <span class="services__break"></span>
      <li>Website Management</li>
    </ul>

    <div class="social">
      <span class="social__item"><span class="social__mark"></span>@trelvanmedia</span>
      <span class="social__item"><span class="social__mark"></span>trelvanmedia</span>
    </div>
  </section>

</main>
</body>
</html>
```